Essential Oil 15ml - package of 6

Design of a box of 6 different essential oils.
+ design of the bottle stickers
My bottles are 15ml clear blue glass.

The pictures attached are my competitors...

Target Market(s)

TERVIK USA

Font styles to use
Serif

Requirements
Must have
• Our logo + "essential oil" and type (lavender, eucalyptus etc....)
• 15ml - 0.50 fl.oz.
• special color for the oil type.

```html
<!DOCTYPE html>
<html lang="en">
<head>
<meta charset="utf-8">
<title>Oren Vale – Pure Essential Oil Labels</title>
<link rel="stylesheet" href="https://fonts.googleapis.com/css2?family=Source+Sans+3:wght@400;700&family=Kalam:wght@400&display=swap">
<style>
  :root {
    --page: #cfcfcf;
    --kraft: #d4bf93;
    --kraft-line: #a8915f;
    --ink-light: #ffffff;
    --oil-orange: #a64f22;
    --oil-rosemary: #521b21;
    --oil-peppermint: #486a72;
    --oil-lavender: #452753;
    --oil-teatree: #767433;
    --oil-eucalyptus: #48623e;
  }
  * { box-sizing: border-box; margin: 0; padding: 0; }
  html, body {
    width: 1200px; height: 623px; overflow: hidden;
    background: var(--page);
  }
  .label-sheet { position: relative; width: 1200px; height: 623px; }
  .label {
    position: absolute;
    width: 586px; height: 187px;
    background: var(--kraft);
    overflow: hidden;
    font-family: "Source Sans 3", "Segoe UI", sans-serif;
    color: var(--ink-light);
    text-align: center;
  }
  .label.col-1 { left: 13px; }
  .label.col-2 { left: 606px; width: 584px; }
  .label.row-1 { top: 14px; }
  .label.row-2 { top: 222px; height: 184px; }
  .label.row-3 { top: 422px; height: 188px; }

  .label.sweet-orange { --oil: var(--oil-orange); }
  .label.rosemary { --oil: var(--oil-rosemary); }
  .label.peppermint { --oil: var(--oil-peppermint); }
  .label.lavender { --oil: var(--oil-lavender); }
  .label.tea-tree { --oil: var(--oil-teatree); }
  .label.eucalyptus { --oil: var(--oil-eucalyptus); }

  .oil-band {
    position: absolute; left: 0; right: 0; top: 111px; bottom: 0;
    background: var(--oil);
  }
  .brand-mark {
    position: absolute; left: 50%; top: 6px;
    width: 40px; height: 40px; margin-left: -20px;
    border-radius: 50%;
    background: var(--ink-light);
  }
  .brand-name {
    position: absolute; left: 0; right: 0; top: 47px;
    font-size: 24px; font-weight: 700; line-height: 30px;
  }
  .oil-badge {
    position: absolute; left: 50%; top: 80px;
    width: 160px; height: 66px; margin-left: -80px;
  }
  .oil-badge svg { display: block; width: 160px; height: 66px; }
  .badge-frame { fill: var(--kraft); stroke: var(--kraft-line); stroke-width: 0.8; }
  .badge-field { fill: var(--oil); }
  .oil-name {
    position: absolute; left: 0; right: 0; top: 0;
    height: 66px; line-height: 66px;
    font-family: "Kalam", "Comic Sans MS", cursive;
    font-size: 16px; letter-spacing: 1px;
  }
  .oil-name.title-case { font-size: 22px; letter-spacing: 0.5px; }
  .product-type {
    position: absolute; left: 0; right: 0; top: 148px;
    font-size: 16px; line-height: 20px;
  }
  .volume {
    position: absolute; left: 0; right: 0; top: 169px;
    font-size: 11px; line-height: 14px;
  }
  .row-2 .product-type { top: 145px; } .row-2 .volume { top: 166px; }
</style>
</head>
<body>
<main class="label-sheet">

  <section class="label col-1 row-1 sweet-orange">
    <div class="oil-band"></div>
    <span class="brand-mark"></span>
    <p class="brand-name">Oren Vale</p>
    <div class="oil-badge">
      <svg viewBox="0 0 160 66"><path class="badge-frame" d="M80 1 C84 8 96 10 110 10 C146 10 158 21 158 33 C158 45 146 56 110 56 C96 56 84 58 80 65 C76 58 64 56 50 56 C14 56 2 45 2 33 C2 21 14 10 50 10 C64 10 76 8 80 1 Z"/><ellipse class="badge-field" cx="80" cy="33" rx="68" ry="19"/></svg>
      <p class="oil-name">SWEET ORANGE</p>
    </div>
    <p class="product-type">Pure Essential Oil</p>
    <p class="volume">15ml (0.50 fl.oz)</p>
  </section>

  <section class="label col-2 row-1 rosemary">
    <div class="oil-band"></div>
    <span class="brand-mark"></span>
    <p class="brand-name">Oren Vale</p>
    <div class="oil-badge">
      <svg viewBox="0 0 160 66"><path class="badge-frame" d="M80 1 C84 8 96 10 110 10 C146 10 158 21 158 33 C158 45 146 56 110 56 C96 56 84 58 80 65 C76 58 64 56 50 56 C14 56 2 45 2 33 C2 21 14 10 50 10 C64 10 76 8 80 1 Z"/><ellipse class="badge-field" cx="80" cy="33" rx="68" ry="19"/></svg>
      <p class="oil-name">ROSEMARY</p>
    </div>
    <p class="product-type">Pure Essential Oil</p>
    <p class="volume">15ml (0.50 fl.oz)</p>
  </section>

  <section class="label col-1 row-2 peppermint">
    <div class="oil-band"></div>
    <span class="brand-mark"></span>
    <p class="brand-name">Oren Vale</p>
    <div class="oil-badge">
      <svg viewBox="0 0 160 66"><path class="badge-frame" d="M80 1 C84 8 96 10 110 10 C146 10 158 21 158 33 C158 45 146 56 110 56 C96 56 84 58 80 65 C76 58 64 56 50 56 C14 56 2 45 2 33 C2 21 14 10 50 10 C64 10 76 8 80 1 Z"/><ellipse class="badge-field" cx="80" cy="33" rx="68" ry="19"/></svg>
      <p class="oil-name">PEPPERMINT</p>
    </div>
    <p class="product-type">Pure Essential Oil</p>
    <p class="volume">15ml (0.50 fl.oz)</p>
  </section>

  <section class="label col-2 row-2 lavender">
    <div class="oil-band"></div>
    <span class="brand-mark"></span>
    <p class="brand-name">Oren Vale</p>
    <div class="oil-badge">
      <svg viewBox="0 0 160 66"><path class="badge-frame" d="M80 1 C84 8 96 10 110 10 C146 10 158 21 158 33 C158 45 146 56 110 56 C96 56 84 58 80 65 C76 58 64 56 50 56 C14 56 2 45 2 33 C2 21 14 10 50 10 C64 10 76 8 80 1 Z"/><ellipse class="badge-field" cx="80" cy="33" rx="68" ry="19"/></svg>
      <p class="oil-name title-case">Lavender</p>
    </div>
    <p class="product-type">Pure Essential Oil</p>
    <p class="volume">15ml (0.50 fl.oz)</p>
  </section>

  <section class="label col-1 row-3 tea-tree">
    <div class="oil-band"></div>
    <span class="brand-mark"></span>
    <p class="brand-name">Oren Vale</p>
    <div class="oil-badge">
      <svg viewBox="0 0 160 66"><path class="badge-frame" d="M80 1 C84 8 96 10 110 10 C146 10 158 21 158 33 C158 45 146 56 110 56 C96 56 84 58 80 65 C76 58 64 56 50 56 C14 56 2 45 2 33 C2 21 14 10 50 10 C64 10 76 8 80 1 Z"/><ellipse class="badge-field" cx="80" cy="33" rx="68" ry="19"/></svg>
      <p class="oil-name">TEA TREE</p>
    </div>
    <p class="product-type">Pure Essential Oil</p>
    <p class="volume">15ml (0.50 fl.oz)</p>
  </section>

  <section class="label col-2 row-3 eucalyptus">
    <div class="oil-band"></div>
    <span class="brand-mark"></span>
    <p class="brand-name">Oren Vale</p>
    <div class="oil-badge">
      <svg viewBox="0 0 160 66"><path class="badge-frame" d="M80 1 C84 8 96 10 110 10 C146 10 158 21 158 33 C158 45 146 56 110 56 C96 56 84 58 80 65 C76 58 64 56 50 56 C14 56 2 45 2 33 C2 21 14 10 50 10 C64 10 76 8 80 1 Z"/><ellipse class="badge-field" cx="80" cy="33" rx="68" ry="19"/></svg>
      <p class="oil-name">EUCALYLPTUS</p>
    </div>
    <p class="product-type">Pure Essential Oil</p>
    <p class="volume">15ml (0.50 fl.oz)</p>
  </section>

</main>
</body>
</html>
```